Business Card Design for Marketing Firm

Looking for business card design for higher end marketing firm. Clean but impressionable/trendy. We are a marketing firm that represents manufacturers in the foodservice equipment and supply industry. Our customers are end users such has hotels, restaurants, country clubs, convention centers and casinos as well as distributors of restaurants supplies and equipment, and manufacturers of foodservice equipment and supplies.
Target Market(s)
Hotels, Restaurants, Supply & Equipment Distributors, Foodservice Manufacturers
Industry/Entity Type
Foodservice/Hospitality
Contact Information for Business Card
Name, Title, Contact Number, Email, Website, Social Media, Address
Requirements
Must have
- Clean & Simple but Serious and Impressionable

```html
<!DOCTYPE html>
<html lang="en">
<head>
<meta charset="utf-8">
<title>Meridian Hospitality Reps – Business Card</title>
<link rel="stylesheet" href="https://fonts.googleapis.com/css2?family=Cinzel:wght@700&family=Arimo:wght@400&display=swap">
<style>
  :root {
    --navy: #0a0a7c;
    --navy-soft: #3b3bc4;
    --paper: #fbfbfb;
    --ink: #1f1f2a;
    --muted: #6a6a72;
    --strip: #c8c9ce;
    --backdrop: #d6d7da;
  }
  * { margin: 0; padding: 0; box-sizing: border-box; }
  html, body { width: 1200px; height: 800px; overflow: hidden; }
  body { background: var(--backdrop); position: relative; font-family: "Arimo", Arial, sans-serif; }

  .card {
    position: absolute;
    width: 600px; height: 343px;
    border-radius: 22px;
    overflow: hidden;
    box-shadow: 0 6px 18px rgba(0,0,0,0.18);
  }
  .card-front { left: 40px; top: 50px; background: var(--paper); }
  .card-back { left: 560px; top: 407px; background: var(--navy); }

  .front-band { position: absolute; inset: 0; width: 100%; height: 100%; }

  .social { position: absolute; left: 30px; top: 30px; display: flex; gap: 6px; }
  .social span { width: 22px; height: 22px; border-radius: 50%; background: var(--navy); display: block; }

  .brand { font-family: "Arimo", Arial, sans-serif; font-weight: 400; white-space: nowrap; }
  .brand-front { position: absolute; right: 40px; top: 70px; font-size: 20px; color: var(--navy); }

  .divider { position: absolute; left: 108px; right: 36px; top: 214px; height: 1px; background: var(--ink); }

  .person { position: absolute; left: 108px; top: 160px; }
  .person-name { font-family: "Cinzel", Georgia, serif; font-weight: 700; font-size: 24px; color: var(--navy); letter-spacing: 0.5px; }
  .person-title { font-size: 14px; color: var(--muted); margin-top: 1px; }

  .contact { position: absolute; left: 108px; top: 224px; font-size: 14.5px; color: var(--ink); line-height: 22px; }
  .contact li { list-style: none; display: flex; align-items: center; gap: 8px; }
  .contact svg { width: 12px; height: 12px; fill: var(--navy); flex: none; }

  .address { position: absolute; right: 40px; top: 224px; font-size: 14.5px; color: var(--ink); line-height: 21px; text-align: right; }
  .web { position: absolute; right: 34px; top: 302px; font-size: 14px; color: #fff; letter-spacing: 3px; }

  .brand-back { position: absolute; left: 0; right: 0; top: 150px; text-align: center; color: var(--navy-soft); font-size: 32px; }
</style>
</head>
<body>
  <section class="card card-front" aria-label="Business card front">
    <svg class="front-band" viewBox="0 0 600 343" preserveAspectRatio="none" aria-hidden="true">
      <path d="M0,320 H334 L344,288 H356 L344,334 H0 Z" fill="var(--strip)"/>
      <path d="M356,288 H600 V343 H0 V332 H344 Z" fill="var(--navy)"/>
    </svg>

    <div class="social" aria-label="Social media"><span></span><span></span><span></span></div>

    <div class="brand brand-front">Meridian Hospitality Reps</div>

    <div class="person">
      <div class="person-name">DANIEL PORTER</div>
      <div class="person-title">President</div>
    </div>
    <div class="divider"></div>

    <ul class="contact">
      <li><svg viewBox="0 0 24 24"><path d="M6.6 10.8a15.1 15.1 0 0 0 6.6 6.6l2.2-2.2a1 1 0 0 1 1-.25 11.4 11.4 0 0 0 3.6.57 1 1 0 0 1 1 1V20a1 1 0 0 1-1 1A17 17 0 0 1 3 4a1 1 0 0 1 1-1h3.5a1 1 0 0 1 1 1c0 1.25.2 2.45.57 3.6a1 1 0 0 1-.25 1z"/></svg>(555) 0142-3388</li>
      <li><svg viewBox="0 0 24 24"><path d="M2 5h20v14H2z M2 5l10 8 10-8" /></svg>name@MERIDIAN.com</li>
    </ul>

    <div class="address">4127 Harbor Lane Drive<br>Lakeview, NY 10000</div>
    <div class="web">www.MERIDIAN.com</div>
  </section>

  <section class="card card-back" aria-label="Business card back">
    <div class="brand brand-back">Meridian Hospitality Reps</div>
  </section>
</body>
</html>
```